Dietitian needs awesome business card

I need a contemporary design that's eye catching but professional.
My card is to given to doctors, specialists and patients alike.
I manage patients with chronic diseases
I have uploaded my logo and current business card, I would also like the other Certified Clinical Nutritionist logo incorporated into the design

Target Market(s)

Doctors, specialists and patients

Industry/Entity Type

Healthcare

Contact Information for Business Card

www.brightfieldnutrition.com.au
Ph: 0427 561 903
Fax: 6457 2183
email: marcus.k.diet@fernmail.com
Space on the back of the card with: Appointment date, Appointment time and appointment location

Font styles to use
Serif

Colors
fbee3e
876aae
ffc214

Requirements
Must have
• My Logo
• Certified Clinical Nutritionist Logo
• My 4 locations - Pinebrook Medical Centre, North Corrin Health, Hollis Medical, Ashcombe Doctors Surgery
Nice to have
• I like the colours in my current business card

```html
<!DOCTYPE html>
<html lang="en">
<head>
<meta charset="utf-8">
<title>Brightfield Nutrition &amp; Dietetics – Business Card</title>
<link rel="stylesheet" href="https://fonts.googleapis.com/css2?family=Arimo:wght@400;700&display=swap">
<style>
  :root {
    --bg: #e9e9ea;
    --paper: #ffffff;
    --ink-blue: #2a3f9e;
    --deep-blue: #1c2f96;
    --mid-blue: #1565c8;
    --cyan: #1f9ad8;
    --lime: #8cc63f;
    --leaf: #5fae2e;
    --orange: #f47a20;
    --rule: #b9bcc6;
    --white: #ffffff;
  }
  * { box-sizing: border-box; margin: 0; padding: 0; }
  html, body { width: 1200px; height: 950px; overflow: hidden; }
  body {
    background: var(--bg);
    font-family: "Arimo", sans-serif;
    position: relative;
  }
  .card {
    position: absolute;
    left: 290px;
    width: 620px;
    height: 354px;
    border-radius: 4px;
    overflow: hidden;
    box-shadow: 0 6px 18px rgba(0,0,0,.18);
  }
  /* ---------- back: appointment side ---------- */
  .card-back { top: 70px; background: var(--paper); }
  .brand {
    position: absolute;
    display: flex;
    align-items: center;
    gap: 10px;
  }
  .brand-dot {
    width: 38px; height: 38px;
    border-radius: 50%;
    background: var(--lime);
    flex: none;
  }
  .brand-name {
    color: var(--ink-blue);
    font-weight: 400;
    line-height: 1.05;
  }
  .card-back .brand { left: 34px; top: 92px; }
  .card-back .brand-name { font-size: 22px; }
  .card-back .brand-name small { display: block; font-size: 13px; }
  .badge {
    position: absolute;
    right: 34px; top: 26px;
    width: 118px; height: 50px;
    background: var(--orange);
  }
  .rule {
    position: absolute;
    height: 1px;
    background: var(--rule);
  }
  .field-label {
    position: absolute;
    color: var(--ink-blue);
    font-size: 15px;
  }
  .ampm {
    position: absolute;
    color: var(--ink-blue);
    font-size: 11px;
  }
  .locations {
    position: absolute;
    list-style: none;
    color: var(--ink-blue);
    font-size: 14px;
  }
  .locations li { display: flex; align-items: center; gap: 8px; margin-bottom: 6px; }
  .locations li::before {
    content: "";
    width: 11px; height: 11px;
    border: 1.5px solid var(--ink-blue);
    flex: none;
  }
  /* ---------- front: identity side ---------- */
  .card-front {
    top: 520px;
    background:
      radial-gradient(circle at 18% 60%, var(--cyan) 0%, rgba(31,154,216,0) 45%),
      linear-gradient(125deg, var(--deep-blue) 0%, var(--mid-blue) 50%, var(--lime) 78%, #b7dd4a 100%);
  }
  .halo {
    position: absolute;
    left: 330px; top: -20px;
    width: 330px; height: 330px;
    border-radius: 50%;
    background: rgba(255,255,255,.9);
  }
  .card-front .brand { left: 370px; top: 112px; }
  .card-front .brand-name { font-size: 30px; }
  .card-front .brand-name small { display: block; font-size: 15px; }
  .person {
    position: absolute;
    left: 40px; top: 130px;
    color: var(--white);
  }
  .person-name { font-size: 22px; font-weight: 700; }
  .person-role { font-size: 14px; font-weight: 700; margin-top: 6px; }
  .contact {
    position: absolute;
    left: 40px; bottom: 30px;
    list-style: none;
    color: var(--white);
    font-size: 14px;
    line-height: 1.55;
  }
</style>
</head>
<body>

  <section class="card card-back" aria-label="Appointment side">
    <div class="brand">
      <span class="brand-dot"></span>
      <span class="brand-name">Brightfield<small>Nutrition &amp; Dietetics</small></span>
    </div>
    <div class="badge" role="img" aria-label="Certified Clinical Nutritionist badge"></div>

    <div class="rule" style="left:240px; top:110px; width:340px;"></div>
    <div class="rule" style="left:240px; top:150px; width:340px;"></div>
    <div class="rule" style="left:34px; top:190px; width:220px;"></div>
    <span class="field-label" style="left:320px; top:175px;">Time :</span>
    <div class="rule" style="left:370px; top:190px; width:210px;"></div>
    <span class="ampm" style="left:545px; top:160px;">AM/PM</span>
    <div class="rule" style="left:34px; top:230px; width:220px;"></div>
    <span class="field-label" style="left:34px; top:258px;">Date :</span>
    <div class="rule" style="left:82px; top:273px; width:172px;"></div>

    <ul class="locations" style="left:34px; top:290px;">
      <li>Pinebrook Medical Centre</li>
      <li>North Corrin Health</li>
    </ul>
    <ul class="locations" style="left:320px; top:210px;">
      <li>Ashcombe Doctors Surgery</li>
      <li>Hollis Medical</li>
    </ul>
  </section>

  <section class="card card-front" aria-label="Identity side">
    <div class="halo"></div>
    <div class="brand">
      <span class="brand-dot"></span>
      <span class="brand-name">Brightfield<small>Nutrition &amp; Dietetics</small></span>
    </div>
    <div class="person">
      <p class="person-name">Marcus Kellaway</p>
      <p class="person-role">Nutritionist &amp; Chef</p>
    </div>
    <ul class="contact">
      <li>P : 0427 561 903</li>
      <li>F : 6457 2183</li>
      <li>marcus.k.diet@fernmail.com</li>
      <li>www.brightfieldnutrition.com.au</li>
    </ul>
  </section>

</body>
</html>
```